Business card for law firm

Need business card for new law firm. Think confident, authoritative, conservative, but not stuffy or old-fashioned.

Contact Information for Business Card

Content for card - logo (uploaded), plus the following:

Paul Whitcombe (larger font)
Managing Partner (larger font, but not as large as name)
Level 9, 7 Ferris Lane
Sydney NSW 2000
Main Tel 02 9364 2710
Direct Tel 02 8472 3159
Email paul@qvlegal.com.au
www.qvlegal.com.au

Letterhead design should include logo plus:
Level 9, 7 Ferris Lane
Sydney NSW 2000
Tel 02 8472 3159
www.qvlegal.com.au

```html
<!DOCTYPE html>
<html lang="en">
<head>
<meta charset="utf-8">
<title>QV Legal – Business Card</title>
<link rel="stylesheet" href="https://fonts.googleapis.com/css2?family=Libre+Baskerville:wght@400;700&family=Montserrat:wght@400;500&display=swap">
<style>
  :root {
    --navy: #1c2266;
    --navy-deep: #171c55;
    --paper: #ffffff;
    --ink: #1c2266;
    --backdrop: #3a3b40;
    --soft: #e8e9ef;
  }
  * { box-sizing: border-box; margin: 0; padding: 0; }
  html, body { width: 1200px; height: 900px; overflow: hidden; }
  body {
    background: var(--backdrop);
    display: flex;
    flex-direction: column;
    align-items: center;
    justify-content: center;
    gap: 40px;
    font-family: "Montserrat", sans-serif;
  }
  .card {
    width: 700px;
    height: 400px;
    position: relative;
    box-shadow: 0 10px 30px rgba(0,0,0,.45);
  }
  .card-front {
    background: var(--paper);
    display: flex;
    align-items: center;
    padding: 0 50px 0 56px;
  }
  .brand {
    width: 300px;
    display: flex;
    align-items: center;
    gap: 14px;
  }
  .brand-mark {
    width: 38px; height: 38px;
    background: var(--navy);
    flex: none;
  }
  .brand-name {
    font-family: "Libre Baskerville", serif;
    font-weight: 400;
    font-size: 40px;
    letter-spacing: 2px;
    color: var(--ink);
    text-transform: uppercase;
  }
  .details {
    flex: 1;
    color: var(--ink);
    padding-left: 30px;
  }
  .person-name {
    font-family: "Libre Baskerville", serif;
    font-weight: 700;
    font-size: 25px;
    text-transform: uppercase;
    letter-spacing: .5px;
    line-height: 1.1;
  }
  .person-role {
    font-size: 17px;
    margin-top: 4px;
  }
  .rule {
    height: 2px;
    background: var(--navy);
    margin: 16px 0;
  }
  .address { font-size: 17px; line-height: 1.4; }
  .contact-list { list-style: none; font-size: 17px; line-height: 1.45; }
  .contact-list li { display: flex; align-items: center; gap: 10px; }
  .contact-list svg { width: 14px; height: 14px; flex: none; }
  .card-back {
    background: linear-gradient(135deg, var(--navy) 0%, var(--navy-deep) 100%);
  }
  .back-brand {
    position: absolute;
    left: 50%; top: 44%;
    transform: translate(-50%, -50%);
    display: flex; align-items: center; gap: 18px;
  }
  .back-brand .brand-mark { background: var(--soft); width: 50px; height: 50px; }
  .back-brand .brand-name { color: var(--soft); font-size: 54px; }
  .back-url {
    position: absolute;
    right: 44px; bottom: 36px;
    color: var(--soft);
    font-size: 15px;
    letter-spacing: 5px;
  }
</style>
</head>
<body>
  <section class="card card-front">
    <div class="brand">
      <span class="brand-mark"></span>
      <span class="brand-name">QV Legal</span>
    </div>
    <div class="details">
      <h1 class="person-name">Paul Whitcombe</h1>
      <p class="person-role">Managing Partner</p>
      <div class="rule"></div>
      <p class="address">Level 9, 7 Ferris Lane<br>Sydney NSW 2000</p>
      <div class="rule"></div>
      <ul class="contact-list">
        <li><svg viewBox="0 0 16 16"><path d="M4 1l3 3-2 2c1 2 3 4 5 5l2-2 3 3-2 3C7 15 1 9 1 3z" fill="var(--navy)"/></svg>02 9364 2710</li>
        <li><svg viewBox="0 0 16 16"><rect x="4" y="1" width="8" height="14" rx="1.5" fill="none" stroke="var(--navy)" stroke-width="2"/><circle cx="8" cy="12" r="1" fill="var(--navy)"/></svg>02 8472 3159</li>
        <li><svg viewBox="0 0 16 16"><rect x="1" y="3" width="14" height="10" fill="none" stroke="var(--navy)" stroke-width="1.6"/><path d="M1 3l7 6 7-6" fill="none" stroke="var(--navy)" stroke-width="1.6"/></svg>paul@qvlegal.com.au</li>
        <li><svg viewBox="0 0 16 16"><circle cx="8" cy="8" r="7" fill="none" stroke="var(--navy)" stroke-width="1.6"/><path d="M1 8h14M8 1c-3 4-3 10 0 14M8 1c3 4 3 10 0 14" fill="none" stroke="var(--navy)" stroke-width="1.2"/></svg>www.qvlegal.com.au</li>
      </ul>
    </div>
  </section>

  <section class="card card-back">
    <div class="back-brand">
      <span class="brand-mark"></span>
      <span class="brand-name">QV Legal</span>
    </div>
    <p class="back-url">www.qvlegal.com.au</p>
  </section>
</body>
</html>
```